PeakRoamJourneys

1. Can you describe what your company does?

Please find enclosed documents for your reference about our business doing.

2. Who are your target customers for the website?

Company Positioning: A comprehensive supplier of premier international sports travel and high-end event services.
Core Advantage: Exclusive international partnership resources and an Official Ticketing Assurance System.
Service Standard: One-Stop, High-Quality Service Solutions based on the "An once-in-a-lifetime experience" philosophy.

Our target customers for the website:
Mid-to-High-end Sports Enthusiasts
Corporate Clients
Sports Associations
Please kindly find enclosed for more details about our target customers, I think it's very important to make it clear to you.

3. Do you have an existing domain name / website address?

Yes, I have. I just applied for this new domain and it's totally a new website. www.peakroamjourneys.example

4. In addition to a Home Page, which other pages / sections would you like your website to have:
About Us
Contact Us , Office / Mailing Address
Sports Travel Products( Bucket Lists) : Globe Shield, Royal Quartet, Vantara Games, Football, KHL, Golf, Skiing, Hiking,Galas
Reviews/ Unforgettable Moments
FAQs
Any other page / section you would like: Here is the website for your reference, www.lanewander.example
For each of the pages / sections you’d like to have, please provide the text (and images, if available) you would like to include.
Please recommend 2-3 templates to me, and let me know what kind of text I will provide to every web pages.

5. Which of the below are features and functionalities your website will need:
Image Gallery
Videos
Contact Form
Maps
FAQs
6. Please provide the URLs for the social media profiles you'd like to link to the website.

Do you know Bright Lantern App?

Please let me know anything you need, thank you very much!

Have a good day!

Target Market(s)

Travel for the world-wide sports games and make an once-in-a-lifetime experience

Industry/Entity Type

sports and travel industry

Coding

Number of Pages Required

5+ page

Requirements
Must have
• our logo
Nice to have
• On the homepage, I’d like a banner-style section to prominently showcase the latest products.

```html
<!DOCTYPE html>
<html lang="en">
<head>
<meta charset="utf-8">
<title>PeakRoamJourneys – Sports Travel</title>
<link href="https://fonts.googleapis.com/css2?family=Oswald:wght@500;600;700&family=Poppins:wght@400;500;600&display=swap" rel="stylesheet">
<style>
:root{
  --navy:#0b1f3a;
  --navy-deep:#081830;
  --blue:#0d4a8f;
  --gold:#c9a227;
  --gold-dark:#b08b1a;
  --ink:#1a1a1a;
  --muted:#555;
  --light:#f1f2f4;
  --white:#fff;
}
*{box-sizing:border-box;margin:0;padding:0}
html,body{width:1200px;height:5291px;overflow:hidden}
body{position:relative;background:var(--white);font-family:"Poppins",sans-serif;color:var(--ink)}
.abs{position:absolute}
.head-font{font-family:"Oswald",sans-serif;font-weight:700;text-transform:uppercase;letter-spacing:.5px}
.btn{position:absolute;background:var(--gold);color:var(--navy);font-family:"Poppins",sans-serif;font-weight:600;font-size:15px;border-radius:30px;display:flex;align-items:center;justify-content:center}
.photo{position:absolute}

/* header + hero */
.hero{position:absolute;left:0;top:0;width:1200px;height:720px;background:radial-gradient(ellipse at 50% 55%,#3a3620 0%,#1d2024 45%,#0c1420 100%)}
.header-rule{position:absolute;left:0;top:144px;width:1200px;height:1px;background:rgba(255,255,255,.25)}
.logo{position:absolute;left:143px;top:30px;color:var(--white);font-family:"Oswald",sans-serif;font-weight:600;font-size:30px}
.phone-chip{position:absolute;left:593px;top:28px;width:44px;height:44px;border-radius:50%;background:var(--gold);display:flex;align-items:center;justify-content:center}
.phone-num{position:absolute;left:653px;top:38px;color:var(--white);font-size:16px;font-weight:500}
.nav{position:absolute;left:383px;top:97px;display:flex;gap:26px;color:var(--white);font-size:15px;font-weight:600}
.hero-title{position:absolute;left:0;width:1200px;text-align:center;font-family:"Oswald",sans-serif;font-weight:700;text-transform:uppercase}
.search{position:absolute;left:267px;top:409px;width:668px;height:70px;border:2px solid var(--white);border-radius:40px;color:var(--white);font-size:16px;padding-left:46px;display:flex;align-items:center}
.search-btn{position:absolute;right:14px;top:15px;width:38px;height:38px;border-radius:50%;background:var(--white);display:flex;align-items:center;justify-content:center}

.sport{position:absolute;border-radius:50%}
.sport .pic{position:absolute;border-radius:50%}
.badge{position:absolute;width:76px;height:76px;border-radius:50%;background:var(--blue);border:4px solid var(--white)}
.sport-label{position:absolute;font-weight:500;font-size:17px;text-align:center;width:200px}

/* about */
.about-title{position:absolute;left:649px;top:1228px;font-family:"Oswald",sans-serif;font-weight:700;font-size:42px;line-height:49px;text-transform:uppercase;color:var(--navy)}
.about-title span{color:var(--blue)}
.body-copy{font-size:13.5px;line-height:28px;color:var(--muted)}

/* moments */
.section-title{position:absolute;font-family:"Oswald",sans-serif;font-weight:700;font-size:42px;text-transform:uppercase;color:var(--navy)}
.section-title span{color:var(--blue)}
.card{position:absolute;top:2041px;height:429px;border-radius:4px;overflow:hidden}

/* faq */
.faq{position:absolute;left:286px;width:628px;height:44px;background:var(--white);border-radius:22px;display:flex;align-items:center;justify-content:space-between;padding:0 22px 0 30px;font-size:13px;font-weight:600;color:var(--navy)}
.plus{width:18px;height:18px;border-radius:50%;background:var(--blue);position:relative}
.plus:before,.plus:after{content:"";position:absolute;background:var(--white);left:4px;top:8px;width:10px;height:2px}
.plus:after{left:8px;top:4px;width:2px;height:10px}

/* sponsors */
.sponsor{position:absolute;top:4010px;height:130px}

/* contact */
.field-label{position:absolute;font-size:13px;font-weight:600;color:var(--navy)}
.field{position:absolute;font-size:12px;color:#777;border-bottom:1px solid #bbb;padding-bottom:10px}

/* footer */
.foot-col{position:absolute;top:5013px;font-size:14px;line-height:24px;color:var(--white)}
.foot-col h4{color:var(--gold);font-size:13px;font-weight:600;margin-bottom:12px;text-transform:uppercase}
</style>
</head>
<body>

<!-- HERO -->
<div class="hero" role="img" aria-label="Dark stadium photograph of a footballer in action"></div>
<svg class="abs" style="left:0;top:560px" width="1200" height="170" viewBox="0 0 1200 170" aria-hidden="true">
  <path d="M0 150 Q600 40 1200 150 L1200 170 L0 170 Z" fill="var(--white)"/>
  <path d="M0 150 Q600 40 1200 150 L1200 115 Q600 0 0 115 Z" fill="none"/>
</svg>
<div class="logo">PeakRoamJourneys</div>
<div class="phone-chip">
  <svg width="18" height="18" viewBox="0 0 24 24"><path fill="#0b1f3a" d="M6.6 10.8a15 15 0 0 0 6.6 6.6l2.2-2.2c.3-.3.7-.4 1-.2 1.1.4 2.3.6 3.6.6.6 0 1 .4 1 1V20c0 .6-.4 1-1 1A17 17 0 0 1 3 4c0-.6.4-1 1-1h3.5c.6 0 1 .4 1 1 0 1.3.2 2.5.6 3.6.1.3 0 .7-.2 1z"/></svg>
</div>
<div class="phone-num">+1 (888) 888 8888</div>
<div class="btn" style="left:862px;top:28px;width:192px;height:44px;font-size:14px">Get Custom Quote</div>
<nav class="nav"><span>Home</span><span>About us</span><span>Sports Travel Experience</span><span>Reviews</span><span>FAQ</span><span>Contact Us</span>
  <svg width="16" height="16" viewBox="0 0 24 24" style="margin-top:3px"><circle cx="10" cy="10" r="7" stroke="#fff" stroke-width="3" fill="none"/><path d="M15 15l6 6" stroke="#fff" stroke-width="3"/></svg>
</nav>
<div class="header-rule"></div>
<div class="hero-title" style="top:215px;font-size:90px;line-height:100px;color:var(--gold)">Experience</div>
<div class="hero-title" style="top:314px;font-size:52px;line-height:60px;color:var(--white)">The World's Greatest Sporting Events</div>
<div class="search">Find your Sports Event
  <div class="search-btn"><svg width="16" height="16" viewBox="0 0 24 24"><circle cx="10" cy="10" r="7" stroke="#0b1f3a" stroke-width="3" fill="none"/><path d="M15 15l6 6" stroke="#0b1f3a" stroke-width="3"/></svg></div>
</div>

<!-- sport circles -->
<div class="sport" style="left:158px;top:637px;width:280px;height:310px;background:var(--gold)"></div>
<div class="sport pic" style="left:174px;top:650px;width:256px;height:256px;background:linear-gradient(160deg,#d9e4ee,#6e94b8 60%,#2c4f73)" role="img" aria-label="Skier carving through powder snow"></div>
<div class="badge" style="left:262px;top:905px"></div>
<div class="sport-label" style="left:198px;top:1004px">SKIING</div>

<div class="sport" style="left:762px;top:637px;width:280px;height:310px;background:var(--gold)"></div>
<div class="sport pic" style="left:770px;top:650px;width:256px;height:256px;background:linear-gradient(170deg,#a6c84a,#3f7a20 60%,#1d3a10)" role="img" aria-label="Golf ball on a tee beside a club on green grass"></div>
<div class="badge" style="left:850px;top:905px"></div>
<div class="sport-label" style="left:790px;top:1004px">GOLF</div>

<div class="sport" style="left:404px;top:591px;width:392px;height:392px;background:var(--white);box-shadow:0 10px 30px rgba(0,0,0,.18)"></div>
<div class="sport pic" style="left:420px;top:607px;width:360px;height:360px;background:radial-gradient(circle at 45% 45%,#8a2a2a,#3a3a40 55%,#15181e)" role="img" aria-label="Footballer in red kit striking the ball in a stadium"></div>
<div class="sport" style="left:551px;top:953px;width:98px;height:98px;background:var(--white);box-shadow:0 4px 14px rgba(0,0,0,.15)"></div>
<div class="sport" style="left:559px;top:961px;width:82px;height:82px;background:var(--gold)"></div>
<svg class="abs" style="left:576px;top:978px" width="48" height="48" viewBox="0 0 48 48" aria-hidden="true"><circle cx="24" cy="24" r="20" fill="none" stroke="#0b1f3a" stroke-width="2.5"/><path d="M24 15l8 6-3 9h-10l-3-9z" fill="none" stroke="#0b1f3a" stroke-width="2.5"/></svg>
<div class="sport-label" style="left:500px;top:1070px">FOOTBALL</div>

<!-- ABOUT -->
<div class="photo" style="left:134px;top:1204px;width:462px;height:604px;background:linear-gradient(180deg,#5a5348 0%,#9a9c9a 40%,#c5b090 75%,#d87a3a 100%)" role="img" aria-label="Climber hanging from an overhanging rock at sunset"></div>
<div class="about-title"><span>Premier Sports Travel</span><br>And Event Management<br>Expert</div>
<p class="abs body-copy" style="left:650px;top:1394px;width:430px">Our company has been deeply rooted in the sports and high-end service sector for over a decade, with businesses covering High-end Conference Management and Planning, Sports Event Operation, and, at its core, Sports Travel services.</p>
<div class="abs" style="left:650px;top:1558px;font-size:18px;font-weight:600;color:var(--navy)">Core Value and Competencies:</div>
<div class="abs" style="left:651px;top:1605px;width:12px;height:12px;border-radius:50%;background:var(--gold)"></div>
<p class="abs body-copy" style="left:673px;top:1596px;width:400px;font-size:13px;line-height:26px"><span style="color:var(--gold-dark)">Professional Qualification:</span> Holds an Outbound Travel Operating License issued by the National Tourism Administration, providing legal and reliable international travel service guarantees for clients</p>
<div class="btn" style="left:651px;top:1736px;width:169px;height:46px">View More</div>

<!-- MOMENTS -->
<div class="section-title" style="left:123px;top:1947px"><span>Unforgettable</span> Moments</div>
<div class="btn" style="left:908px;top:1956px;width:169px;height:44px">View More</div>
<div class="card" style="left:125px;width:380px;background:radial-gradient(circle at 55% 45%,#f0a030,#8a3a10 40%,#141820 80%)" role="img" aria-label="Flaming torch lit against stadium lights"></div>
<div class="card" style="left:534px;width:380px;background:linear-gradient(160deg,#2b2e3e,#6a2a2a 45%,#1a2540)" role="img" aria-label="American football players colliding during a tackle"></div>
<div class="abs" style="left:534px;top:2041px;width:380px;height:429px;background:linear-gradient(180deg,transparent 55%,rgba(0,0,0,.75))"></div>
<div class="abs" style="left:559px;top:2344px;color:var(--white);font-size:21px;font-weight:500">2026 Football Moment</div>
<div class="abs" style="left:565px;top:2384px;width:330px;color:var(--white);font-size:13px;line-height:27px">Professional Qualification: Holds an Outbound Travel Operating License issued by</div>
<div class="card" style="left:941px;width:259px;background:linear-gradient(180deg,#9fb5c9,#c9a06a 55%,#4a3a28)" role="img" aria-label="Hikers with poles walking a mountain ridge at dusk"></div>

<!-- VIDEOS -->
<div class="section-title" style="left:0;width:1200px;text-align:center;top:2585px"><span>Our</span> Videos</div>
<svg class="abs" style="left:0;top:2990px" width="1200" height="850" viewBox="0 0 1200 850" aria-hidden="true">
  <path d="M0 70 Q600 -40 1200 70 L1200 845 L0 845 Z" fill="var(--gold)"/>
  <path d="M0 95 Q600 -15 1200 95 L1200 845 L0 845 Z" fill="var(--navy)"/>
</svg>
<div class="abs" style="left:164px;top:2671px;width:872px;height:555px;background:var(--white);border-radius:8px;box-shadow:0 10px 40px rgba(0,0,0,.2)"></div>
<div class="photo" style="left:170px;top:2677px;width:860px;height:543px;border-radius:4px;background:radial-gradient(ellipse at 50% 90%,#3f6a3a,#0f2a48 45%,#050d1c)" role="img" aria-label="Floodlit football stadium at night"></div>
<div class="abs" style="left:560px;top:2886px;width:80px;height:80px;border-radius:50%;background:var(--white);display:flex;align-items:center;justify-content:center">
  <svg width="30" height="30" viewBox="0 0 30 30"><path d="M9 5l16 10-16 10z" fill="#0b1f3a"/></svg>
</div>

<!-- FAQ -->
<div class="section-title" style="left:0;width:1200px;text-align:center;top:3331px;color:var(--white)">Any <span style="color:var(--gold)">Questions ?</span></div>
<div class="faq" style="top:3426px">1.Lorem ipsum dolor sit amet, consectetur adipiscing elit &nbsp;? <i class="plus"></i></div>
<div class="faq" style="top:3488px">2.Lorem ipsum dolor sit amet, consectetur adipiscing elit &nbsp;? <i class="plus"></i></div>
<div class="faq" style="top:3550px">3.Lorem ipsum dolor sit amet, consectetur adipiscing elit &nbsp;? <i class="plus"></i></div>
<div class="faq" style="top:3612px">4.Lorem ipsum dolor sit amet, consectetur adipiscing elit &nbsp;? <i class="plus"></i></div>
<div class="btn" style="left:516px;top:3695px;width:168px;height:44px">View More</div>

<!-- SPONSORS -->
<div class="section-title" style="left:0;width:1200px;text-align:center;top:3918px"><span>Our</span> Sponsors</div>
<div class="sponsor" style="left:222px;width:96px;top:4015px;height:115px;background:var(--blue);border-radius:8px 8px 48px 48px" role="img" aria-label="Sponsor badge"></div>
<div class="sponsor" style="left:400px;width:92px;top:4015px;height:120px;background:#2e8b3a;border-radius:8px 8px 46px 46px" role="img" aria-label="Sponsor badge"></div>
<div class="sponsor" style="left:560px;width:190px;top:4030px;height:90px;background:#1f3c8c;border-radius:6px" role="img" aria-label="Sponsor badge"></div>
<div class="sponsor" style="left:832px;width:150px;top:4020px;height:110px;background:#e08a1e;border-radius:6px" role="img" aria-label="Sponsor badge"></div>

<!-- CONTACT -->
<div class="abs" style="left:0;top:4500px;width:1200px;height:380px;background:var(--light)"></div>
<div class="photo" style="left:111px;top:4283px;width:360px;height:361px;border-radius:4px;background:radial-gradient(circle at 50% 30%,#6f8fb0,#233a58 50%,#0c1626)" role="img" aria-label="Fan with raised arms cheering in a lit stadium"></div>
<div class="abs" style="left:697px;top:4307px;width:302px;height:292px;border:2px solid #555"></div>
<div class="abs" style="left:409px;top:4326px;width:565px;height:386px;background:var(--white);border-radius:8px;box-shadow:0 10px 30px rgba(0,0,0,.12)"></div>
<div class="section-title" style="left:456px;top:4345px;font-size:40px"><span style="color:var(--navy)">Get in</span> <span>Touch</span></div>
<div class="field-label" style="left:457px;top:4412px">YOUR NAME</div>
<div class="field" style="left:457px;top:4446px;width:225px">Jhon Smith</div>
<div class="field-label" style="left:705px;top:4412px">EMAIL</div>
<div class="field" style="left:705px;top:4446px;width:225px">jhon.smith@mail.example</div>
<div class="field-label" style="left:457px;top:4492px">EVENT NAME</div>
<div class="field" style="left:457px;top:4527px;width:225px">Bulb Replacement <span style="float:right">⌄</span></div>
<div class="field-label" style="left:705px;top:4492px">PHONE</div>
<div class="field" style="left:705px;top:4527px;width:225px">+1 (888) 888 8888</div>
<div class="field-label" style="left:457px;top:4577px">MESSAGE</div>
<div class="field" style="left:457px;top:4611px;width:430px">Hi , Do you have Moment To Talk About Us</div>
<div class="abs" style="left:890px;top:4623px;width:44px;height:44px;border-radius:50%;background:var(--gold);display:flex;align-items:center;justify-content:center">
  <svg width="20" height="20" viewBox="0 0 24 24"><path d="M3 11l18-8-8 18-2-8z" fill="#0b1f3a"/></svg>
</div>

<!-- FOOTER -->
<svg class="abs" style="left:0;top:4790px" width="1200" height="501" viewBox="0 0 1200 501" aria-hidden="true">
  <path d="M0 110 Q600 -30 1200 110 L1200 501 L0 501 Z" fill="var(--gold)"/>
  <path d="M0 140 Q600 0 1200 140 L1200 501 L0 501 Z" fill="var(--navy)"/>
</svg>
<div class="abs" style="left:0;width:1200px;top:4895px;text-align:center;color:var(--white);font-family:'Oswald',sans-serif;font-weight:600;font-size:30px">PeakRoamJourneys</div>
<div class="foot-col" style="left:127px"><h4>Connect</h4>Custom Trip Quote<br>Contact Us<br>Sport Specific Updates<br>Email Newsletter<br>Guest Feedback Form</div>
<div class="foot-col" style="left:415px"><h4>Quick Links</h4>Upcoming Events<br>Travel Advisors<br>Guides &amp; Brochures<br>About Us</div>
<div class="foot-col" style="left:674px"><h4>Contact Us</h4>1-800-555-0142<br>+1 (888) 888 8888<br>info@peakroamjourneys.example</div>
<div class="foot-col" style="left:1001px"><h4>Social Media</h4>Fanpage Hub<br>Snapwall<br>ClipStream</div>
<div class="abs" style="left:124px;top:5216px;color:var(--white);font-size:13px">Privacy PolicyTerms &amp; ConditionsSitemapChange Cookie Preference</div>
<div class="abs" style="left:830px;top:5214px;color:var(--white);font-size:13px">Copyright@2025.All Rights Reserved..</div>

</body>
</html>
```